Home Remodeler Needs a Website!

Single page (plus contact form) website for small home remodeling company. He's got a few pictures he'd like on the site and needs some basic text. He likes clean, simple designs and is "more traditional" in his stylistic preferences. Most of his business comes from word-of-mouth advertising and so the site is just something he needs for people to feel more comfortable with his business.

Target Market(s)

People who want to remodel their homes

Coding

Coded - Design and coding required

Number of Pages Required

2 page

Requirements
Must have
• Main page to include some or all of the attached images, contact page. Neutral colors. Old domain: lindcroftmeadowbuild.com New domain: qm-ventureworks.com You can pull text from the old site or update it.
Should not have
• No loud colors/loud visual elements

```html
<!DOCTYPE html>
<html lang="en">
<head>
<meta charset="utf-8">
<title>Lindcroft Meadow Homes</title>
<link href="https://fonts.googleapis.com/css2?family=Cabin:wght@400;500;600;700&display=swap" rel="stylesheet">
<style>
:root{
  --navy:#13132b;
  --nav-bg:#1c1c28;
  --red:#8b0f0f;
  --red-text:#8e1212;
  --gold:#e5b432;
  --lavender:#e1e1fb;
  --pill:#e3e3e3;
  --card:#f0f0f0;
  --ink:#222;
  --body:#444;
  --white:#fff;
  --line:#bbb;
}
*{box-sizing:border-box;margin:0;padding:0}
html,body{width:1200px;height:4161px;overflow:hidden}
body{position:relative;background:var(--white);font-family:"Cabin",Arial,sans-serif;color:var(--ink)}
.abs{position:absolute}
.photo{position:absolute}

/* header */
.site-header{position:absolute;left:0;top:0;width:1200px;height:80px;background:var(--nav-bg);z-index:3}
.brand{position:absolute;left:142px;top:20px;font-size:31px;color:var(--white);font-weight:400}
.main-nav{position:absolute;top:33px;left:0;width:1200px;font-size:14px;color:var(--white)}
.main-nav span{position:absolute}
.main-nav .active{color:var(--gold)}

/* hero */
.hero{position:absolute;left:0;top:0;width:1200px;height:700px;overflow:hidden}
.hero-photo{left:0;top:0;width:1200px;height:700px;background:linear-gradient(180deg,#2c2a2e 0%,#3d342e 40%,#2a2426 75%,#1b1a22 100%)}
.hero-shade{position:absolute;inset:0;background:rgba(0,0,0,.25)}
.hero-shape{position:absolute;left:0;top:560px}
.hero-copy{position:absolute;left:0;top:255px;width:1200px;text-align:center;color:var(--white)}
.hero-lead{font-size:32px;line-height:40px;font-weight:400}
.hero-title{font-size:42px;font-weight:700;margin-top:12px;letter-spacing:.3px}
.btn{display:inline-block;background:var(--red);color:var(--white);font-size:15px;font-weight:600;text-transform:uppercase;text-align:center}
.hero .btn{position:absolute;left:540px;top:407px;width:119px;height:36px;line-height:36px}
.hero-arrow{position:absolute;top:332px}

/* welcome */
.section-title{color:var(--red-text);font-weight:500}
.welcome-photo{left:144px;top:777px;width:415px;height:289px;background:linear-gradient(160deg,#f2f2f2,#d9d9d9 60%,#c9c7c2)}
.welcome-title{left:622px;top:768px;font-size:33px;line-height:45px}
.copy{font-size:13px;line-height:27px;color:var(--body)}
.welcome-copy{left:622px;top:870px;width:430px}
.welcome-btn{left:622px;top:1024px;width:119px;height:42px;line-height:42px}

/* services */
.services-band{left:0;top:1185px;width:1200px;height:567px;background:var(--lavender)}
.services-title{left:0;top:1268px;width:1200px;text-align:center;font-size:32px}
.service-card{position:absolute;width:218px;height:158px;background:var(--white);text-align:center}
.service-card svg{position:absolute;left:79px;top:22px}
.service-card span{position:absolute;left:0;top:106px;width:100%;font-size:19px;color:var(--ink)}

/* package */
.package-title{left:0;top:1840px;width:1200px;text-align:center;font-size:33px}
.package-item{position:absolute;left:144px;width:439px;height:62px;border-radius:31px;background:var(--pill);font-size:20px;color:#333}
.package-item svg{position:absolute;left:26px;top:13px}
.package-item span{position:absolute;left:85px;top:18px}
.package-item.active{background:var(--white);border:2px solid var(--red-text);color:var(--red-text)}
.package-item.active span{top:16px}
.package-item .go{position:absolute;right:0;top:0;width:42px;height:58px;border-left:1px solid var(--line)}
.package-card{left:622px;top:1917px;width:434px;height:420px;background:var(--card)}
.package-photo{left:0;top:0;width:434px;height:249px;background:linear-gradient(135deg,#c7532c 0%,#a69a87 45%,#6d6860 100%)}
.package-card h3{position:absolute;left:23px;top:270px;font-size:24px;font-weight:500;color:var(--ink)}
.package-card p{position:absolute;left:23px;top:310px;width:392px;font-size:11px;line-height:21px;color:#777}
.package-card a{position:absolute;left:23px;top:383px;font-size:11px;color:var(--ink);text-decoration:underline;font-weight:600}

/* tinker */
.tinker-band{left:0;top:2440px;width:1200px;height:459px;background:var(--lavender)}
.tinker-photo{left:144px;top:2526px;width:415px;height:291px;background:linear-gradient(140deg,#e0b07a,#b8855a 55%,#3d4a73)}
.tinker-title{left:620px;top:2518px;font-size:33px}
.tinker-copy{left:622px;top:2565px;width:435px}
.tinker-btn{left:622px;top:2773px;width:119px;height:42px;line-height:42px}

/* gallery */
.gallery-tile{position:absolute;overflow:hidden}
.gallery-tile .label{position:absolute;left:0;bottom:0;background:var(--navy);color:var(--white);font-size:19px;padding:6px 13px 5px}
.gallery-track{left:0;top:3605px;width:1200px;height:10px;background:#c9c9c9}
.gallery-progress{left:0;top:3605px;width:239px;height:10px;background:var(--red)}

/* contact */
.contact-title{left:144px;top:3700px;font-size:29px}
.field{position:absolute;border:1px solid #c8c8c8;background:var(--white);font-size:10px;color:#555;padding:12px 0 0 15px}
.submit{left:144px;top:3937px;width:81px;height:39px;line-height:39px;font-size:15px;text-transform:none}
.info-title{left:677px;top:3700px;font-size:29px}
.info-row{position:absolute;left:677px;font-size:22px;color:var(--ink)}
.info-row svg{position:absolute;left:0;top:5px}
.info-row span{position:absolute;left:38px;top:0;white-space:nowrap}

/* footer */
.site-footer{left:0;top:4063px;width:1200px;height:98px;background:var(--navy);color:#c9c9dd}
.footer-links{position:absolute;left:144px;top:25px;font-size:11px}
.footer-links i{font-style:normal;margin:0 8px}
.copyright{position:absolute;left:144px;top:57px;font-size:10px}
.social{position:absolute;top:37px;width:22px;height:22px;border:2px solid #8e8eb6;border-radius:50%}
</style>
</head>
<body>

<header class="site-header">
  <div class="brand">Lindcroft Meadow Homes</div>
  <nav class="main-nav">
    <span class="active" style="left:580px">Services</span>
    <span style="left:662px">Resources</span>
    <span style="left:755px">Gallery</span>
    <span style="left:830px">About Us</span>
    <span style="left:919px">Contact Us</span>
    <span style="left:1019px">Extras</span>
  </nav>
</header>

<section class="hero">
  <div class="photo hero-photo" role="img" aria-label="Photo of a dark, freshly remodeled living room with wood floors and French doors"></div>
  <div class="hero-shade"></div>
  <svg class="hero-shape" width="1200" height="140" viewBox="0 0 1200 140">
    <polygon points="0,128 840,30 1200,130 1200,140 0,140" fill="#14143a"/>
    <polygon points="0,140 840,40 1200,140" fill="#ffffff"/>
  </svg>
  <svg class="hero-arrow" style="left:46px" width="20" height="30" viewBox="0 0 20 30"><polyline points="16,3 4,15 16,27" fill="none" stroke="#fff" stroke-width="4"/></svg>
  <svg class="hero-arrow" style="left:1132px" width="20" height="30" viewBox="0 0 20 30"><polyline points="4,3 16,15 4,27" fill="none" stroke="#fff" stroke-width="4"/></svg>
  <div class="hero-copy">
    <div class="hero-lead">When you want affordable, quality<br>home construction services</div>
    <div class="hero-title">THINK OF US TO DO THE JOB</div>
  </div>
  <a class="btn">Read More</a>
</section>

<section>
  <div class="photo welcome-photo" role="img" aria-label="Photo of a bright attic room under renovation with a yellow ladder"></div>
  <h2 class="abs section-title welcome-title">Welcome to<br>Lindcroft Meadow Homes</h2>
  <p class="abs copy welcome-copy">Since 1981 Gordon Ashby has built and remodeled over 400 homes and businesses. Let us be your contractor for the next project you start. When quality, value and personal attention to detail are important With over 20 years experience in residential and commercial construction, you can trust your project to Lindcroft Meadow Homes.</p>
  <a class="abs btn welcome-btn">Read More</a>
</section>

<section>
  <div class="abs services-band"></div>
  <h2 class="abs section-title services-title">Services</h2>

  <div class="service-card" style="left:144px;top:1326px">
    <svg width="60" height="60" viewBox="0 0 60 60" fill="none" stroke="#333" stroke-width="2"><path d="M30 4 L4 52 H56 Z M30 4 V52 M17 28 H43 M10 40 H50 M17 28 L30 52 L43 28"/></svg>
    <span>Roofing</span></div>
  <div class="service-card" style="left:375px;top:1326px">
    <svg width="60" height="60" viewBox="0 0 60 60" fill="none" stroke="#333" stroke-width="2"><rect x="8" y="4" width="44" height="52"/><path d="M30 4 V56 M8 30 H52 M14 14 l4 -4 M38 42 l4 -4"/></svg>
    <span>Window Replacement</span></div>
  <div class="service-card" style="left:607px;top:1326px">
    <svg width="60" height="60" viewBox="0 0 60 60" fill="none" stroke="#333" stroke-width="2"><rect x="4" y="12" width="30" height="42"/><rect x="9" y="18" width="20" height="12"/><path d="M9 38 h4 M17 38 h4 M25 38 h4 M9 46 h4 M17 46 h4 M25 46 h4"/><circle cx="48" cy="10" r="5"/><path d="M40 28 h14 M40 36 h12 M40 44 h14"/></svg>
    <span>Electrical</span></div>
  <div class="service-card" style="left:838px;top:1326px">
    <svg width="60" height="60" viewBox="0 0 60 60" fill="none" stroke="#333" stroke-width="2"><rect x="4" y="6" width="52" height="18" rx="2"/><path d="M10 18 H50 M22 32 v8 M30 32 v8 M38 32 v8 M12 44 l6 6 M18 44 l-6 6 M42 44 l6 6 M48 44 l-6 6"/></svg>
    <span>Air Conditioning</span></div>

  <div class="service-card" style="left:144px;top:1502px">
    <svg width="60" height="60" viewBox="0 0 60 60" fill="none" stroke="#333" stroke-width="2"><path d="M6 14 H34 V26 H46 V56 H34 V38 H22 V26 H6 Z"/><circle cx="14" cy="8" r="5"/><path d="M42 8 q4 6 0 10 q-4 -4 0 -10"/></svg>
    <span>Plumbing Upgrades</span></div>
  <div class="service-card" style="left:375px;top:1502px">
    <svg width="60" height="60" viewBox="0 0 60 60" fill="none" stroke="#333" stroke-width="2"><path d="M36 4 L54 22 L40 30 L28 18 Z M34 26 L10 50 a4 4 0 0 0 6 6 L40 32"/><path d="M48 30 v20"/></svg>
    <span>Painting</span></div>
  <div class="service-card" style="left:607px;top:1502px">
    <svg width="60" height="60" viewBox="0 0 60 60" fill="none" stroke="#333" stroke-width="2"><path d="M6 56 V4 H22 V16 M22 16 H34 V30 M6 30 H34 M14 40 h14 l6 6 v10 M34 46 q10 0 14 10 H34"/></svg>
    <span>Gutters</span></div>
  <div class="service-card" style="left:838px;top:1502px">
    <svg width="60" height="60" viewBox="0 0 60 60" fill="none" stroke="#333" stroke-width="2"><ellipse cx="22" cy="22" rx="18" ry="14"/><path d="M38 24 h10 l8 12 v10 H4 v-10 h34 z"/><circle cx="14" cy="48" r="5"/><circle cx="46" cy="48" r="5"/></svg>
    <span>Concrete Work</span></div>
</section>

<section>
  <h2 class="abs section-title package-title">All in one package</h2>

  <div class="package-item active" style="top:1914px">
    <svg width="40" height="34" viewBox="0 0 40 34" fill="none" stroke="#8e1212" stroke-width="1.6"><rect x="2" y="2" width="36" height="30"/><path d="M2 9 H38 M8 15 h10 v12 H8 z M22 15 h10 M22 21 h10 M22 27 h10"/></svg>
    <span>Pre Construction Consultation</span>
    <div class="go"><svg style="left:9px;top:19px" width="20" height="20" viewBox="0 0 20 20"><circle cx="10" cy="10" r="10" fill="#7f7f92"/><polyline points="8,5 13,10 8,15" fill="none" stroke="#fff" stroke-width="2"/></svg></div>
  </div>
  <div class="package-item" style="top:1986px">
    <svg width="40" height="34" viewBox="0 0 40 34" fill="none" stroke="#444" stroke-width="1.6"><path d="M2 16 L20 2 L38 16 M6 13 V32 H34 V13 M14 32 V22 H26 V32"/></svg>
    <span>New Construction</span></div>
  <div class="package-item" style="top:2058px">
    <svg width="40" height="34" viewBox="0 0 40 34" fill="none" stroke="#444" stroke-width="1.6"><rect x="2" y="14" width="36" height="18"/><path d="M2 22 H38 M14 14 V32 M26 14 V32 M8 2 v8 M30 4 h6 v10"/></svg>
    <span>Remodeling / kitchens and baths</span></div>
  <div class="package-item" style="top:2130px">
    <svg width="40" height="34" viewBox="0 0 40 34" fill="none" stroke="#444" stroke-width="1.6"><rect x="2" y="2" width="28" height="30"/><path d="M8 8 h8 v8 H8 z M8 22 h8 v10 M30 14 h8 v18 h-8"/></svg>
    <span>Additions</span></div>
  <div class="package-item" style="top:2202px">
    <svg width="40" height="34" viewBox="0 0 40 34" fill="none" stroke="#444" stroke-width="1.6"><path d="M2 32 H38 M6 32 V6 H18 V14 H26 V22 H34 V32"/></svg>
    <span>Porches and Decks</span></div>
  <div class="package-item" style="top:2274px">
    <svg width="40" height="34" viewBox="0 0 40 34" fill="none" stroke="#444" stroke-width="1.6"><path d="M2 10 L20 2 L38 10 Z M4 12 H36 M8 14 V28 M16 14 V28 M24 14 V28 M32 14 V28 M2 30 H38"/></svg>
    <span>Specializing in historic renovations</span></div>

  <div class="abs package-card">
    <div class="photo package-photo" role="img" aria-label="Photo of a builder and clients reviewing plans together"></div>
    <h3>Pre Construction Consultation</h3>
    <p>Vestibulum condimentum, risus ut posuere cursus, velit justo accumsan sem, lobortis aliquet metus dui eu libero. Pellentesque a imperdiet dolor, et auctor est. Fusce sollicitudin lorem et luctus volutpat.</p>
    <a>READ MORE</a>
  </div>
</section>

<section>
  <div class="abs tinker-band"></div>
  <div class="photo tinker-photo" role="img" aria-label="Photo of a framer working among new timber roof framing"></div>
  <h2 class="abs section-title tinker-title">Don't tinker around</h2>
  <p class="abs copy tinker-copy">I have built my business with a partnership of clients, employees, sub-contractors, suppliers and inspectors. Since each project is unique, this partnership brings creative ideas to your home. I have deep "hands on" history in construction from foundations to final finishing touches.<br><br>We cultivate suppliers who deliver quality materials on time and without damage.</p>
  <a class="abs btn tinker-btn">Read More</a>
</section>

<section>
  <div class="gallery-tile" style="left:0;top:2899px;width:399px;height:200px;background:linear-gradient(180deg,#3d4a60,#566070 60%,#4a4a3e)" role="img" aria-label="Photo of a large home at dusk"><span class="label">Proin placerat</span></div>
  <div class="gallery-tile" style="left:0;top:3099px;width:399px;height:201px;background:linear-gradient(135deg,#f1f1f1,#d8d8d8 60%,#bda98f)" role="img" aria-label="Photo of a white marble bathroom with freestanding tub"><span class="label">Suspendisse</span></div>
  <div class="gallery-tile" style="left:399px;top:2899px;width:801px;height:401px;background:linear-gradient(160deg,#1f3f78 0%,#6e6b66 35%,#8a8782 55%,#4b3a2c 80%,#2d2620 100%)" role="img" aria-label="Photo of a remodeled kitchen with steel refrigerator and farmhouse sink"><span class="label">Vestibulum luctus</span></div>
  <div class="gallery-tile" style="left:0;top:3300px;width:399px;height:305px;background:linear-gradient(180deg,#2a2226,#3f2a22 50%,#161314)" role="img" aria-label="Photo of a dark wood home bar"><span class="label">Nulla tristique</span></div>
  <div class="gallery-tile" style="left:399px;top:3300px;width:401px;height:305px;background:linear-gradient(180deg,#e9e6e0,#d8cfc2 60%,#c8b49a)" role="img" aria-label="Photo of a light kitchen with bar stools"><span class="label">Duis ornare</span></div>
  <div class="gallery-tile" style="left:800px;top:3300px;width:400px;height:305px;background:linear-gradient(180deg,#7c8794,#5b6570 55%,#3f3a36)" role="img" aria-label="Photo of a bathroom with glass shower and skylight"><span class="label">Nam tempus</span></div>
  <div class="abs gallery-track"></div>
  <div class="abs gallery-progress"></div>
</section>

<section>
  <h2 class="abs section-title contact-title">Contact Us</h2>
  <div class="field" style="left:144px;top:3753px;width:217px;height:37px">Name</div>
  <div class="field" style="left:368px;top:3753px;width:217px;height:37px">Email</div>
  <div class="field" style="left:144px;top:3802px;width:217px;height:37px">Phone</div>
  <div class="field" style="left:368px;top:3802px;width:217px;height:37px">Service for
    <svg style="position:absolute;right:10px;top:15px" width="12" height="7" viewBox="0 0 12 7"><polygon points="0,0 12,0 6,7" fill="#333"/></svg></div>
  <div class="field" style="left:144px;top:3850px;width:441px;height:76px">Message</div>
  <a class="abs btn submit">Submit</a>

  <h2 class="abs section-title info-title">Contact Info</h2>
  <div class="info-row" style="top:3746px">
    <svg width="14" height="18" viewBox="0 0 14 18"><path d="M7 0 a7 7 0 0 1 7 7 c0 5 -7 11 -7 11 s-7 -6 -7 -11 a7 7 0 0 1 7 -7z" fill="#222"/><circle cx="7" cy="7" r="2.6" fill="#fff"/></svg>
    <span>Box 40517, Fairbrook, TN 37990</span></div>
  <div class="info-row" style="top:3814px">
    <svg width="16" height="16" viewBox="0 0 16 16"><path d="M3 0 l3 4 -2 2 c1 3 3 5 6 6 l2 -2 4 3 -2 3 C7 16 0 9 0 3z" fill="#222"/></svg>
    <span>555-014-2873</span></div>
  <div class="info-row" style="top:3882px">
    <svg width="17" height="17" viewBox="0 0 17 17"><rect x="0" y="4" width="4" height="13" fill="#222"/><rect x="5" y="0" width="10" height="5" fill="none" stroke="#222" stroke-width="1.6"/><rect x="5" y="6" width="12" height="11" fill="#222"/><rect x="7" y="8" width="2" height="2" fill="#fff"/><rect x="11" y="8" width="2" height="2" fill="#fff"/><rect x="7" y="12" width="2" height="2" fill="#fff"/><rect x="11" y="12" width="2" height="2" fill="#fff"/></svg>
    <span>555-014-6190</span></div>
  <div class="info-row" style="top:3950px">
    <svg width="18" height="14" viewBox="0 0 18 14"><rect x="0" y="0" width="18" height="14" fill="#222"/><polyline points="0,1 9,8 18,1" fill="none" stroke="#fff" stroke-width="1.5"/></svg>
    <span>gordon@lindcroftmeadowbuild.com</span></div>
</section>

<footer class="abs site-footer">
  <div class="footer-links">Home<i>|</i>Services<i>|</i>Resources<i>|</i>Gallery<i>|</i>About Us<i>|</i>Contact Us<i>|</i>Extras</div>
  <div class="copyright">Copyright &copy; 2021 &nbsp;Lindcroft Meadow Homes. &nbsp;All rights reserved.</div>
  <span class="social" style="left:990px" aria-label="Social link"></span>
  <span class="social" style="left:1033px" aria-label="Social link"></span>
</footer>

</body>
</html>
```